Venture 482 - Lumora Book Cover

I am looking for a Lumora book cover for my book about "Venture 482".
The Book is Titled:
Venture 482 Ascended
Shaping Outcomes: Paths To Unlocking Cosmic Truths
Author is Dorian Pell
Here is a book description that may help you understand more about it:
Inspired by the genius of Edwin Marlowe, this comprehensive guide delves into the ancient wisdom and cutting-edge science behind the 482 method, a powerful tool for manifesting your desires. Whether you're seeking personal growth, financial success, or spiritual enlightenment, this book provides advanced techniques and methods to transform your dreams into reality.
Any questions please ask.
Thanks
Owen

```html
<!DOCTYPE html>
<html lang="en">
<head>
<meta charset="utf-8">
<title>Venture 482 Ascended — Dorian Pell</title>
<link rel="stylesheet" href="https://fonts.googleapis.com/css2?family=Bebas+Neue&family=Questrial&family=Tinos:wght@400;700&display=swap">
<style>
  :root {
    --bg-light: #ececec;
    --bg-mid: #d2d2d2;
    --bg-dark: #b4b4b4;
    --navy: #1c1a3e;
    --indigo: #3b3f82;
    --ink: #111111;
    --art-light: #f1f1f1;
    --art-mid: #c9c9c9;
    --art-dark: #8e8e93;
  }
  * { margin: 0; padding: 0; box-sizing: border-box; }
  html, body { width: 806px; height: 1200px; overflow: hidden; background: var(--bg-mid); }
  .cover {
    position: relative;
    width: 806px;
    height: 1200px;
    overflow: hidden;
    background:
      radial-gradient(ellipse at 50% 0%, var(--bg-light) 0%, rgba(236,236,236,0) 60%),
      linear-gradient(180deg, var(--bg-light) 0%, var(--bg-mid) 55%, var(--bg-dark) 100%);
  }
  .specks { position: absolute; inset: 0; }
  .series-title {
    position: absolute;
    top: 108px;
    left: 0;
    width: 100%;
    text-align: center;
    font-family: "Bebas Neue", sans-serif;
    font-size: 194px;
    line-height: 1;
    color: var(--navy);
    letter-spacing: 1px;
  }
  .emblem-art {
    position: absolute;
    left: 82px;
    top: 268px;
    width: 644px;
    height: 576px;
  }
  .emblem-number {
    position: absolute;
    left: 0;
    top: 502px;
    width: 100%;
    text-align: center;
    font-family: "Questrial", sans-serif;
    font-size: 112px;
    line-height: 1;
    color: var(--ink);
    letter-spacing: 2px;
  }
  .edition {
    position: absolute;
    left: 106px;
    top: 826px;
    width: 596px;
    display: flex;
    justify-content: space-between;
    font-family: "Bebas Neue", sans-serif;
    font-size: 66px;
    line-height: 1;
    color: var(--navy);
  }
  .subtitle {
    position: absolute;
    top: 926px;
    left: 0;
    width: 100%;
    text-align: center;
    font-family: "Tinos", serif;
    color: var(--indigo);
  }
  .subtitle-lead { font-size: 29px; font-weight: 700; letter-spacing: -0.5px; line-height: 36px; }
  .subtitle-body { font-size: 28px; font-weight: 400; line-height: 36px; }
  .author {
    position: absolute;
    left: 76px;
    top: 1098px;
    width: 660px;
    display: flex;
    justify-content: space-between;
    font-family: "Tinos", serif;
    font-size: 62px;
    line-height: 1;
    color: var(--ink);
  }
  .author .gap { width: 24px; }
</style>
</head>
<body>
  <main class="cover">
    <svg class="specks" width="806" height="1200" aria-hidden="true">
      <g fill="#ffffff">
        <circle cx="682" cy="316" r="7" opacity="0.45"/>
        <circle cx="213" cy="276" r="4" opacity="0.5"/>
        <circle cx="744" cy="948" r="5" opacity="0.5"/>
        <circle cx="640" cy="860" r="4" opacity="0.6"/>
        <circle cx="16" cy="770" r="3" opacity="0.7"/>
        <circle cx="266" cy="1176" r="14" opacity="0.35"/>
        <circle cx="752" cy="1088" r="9" opacity="0.5"/>
        <circle cx="550" cy="1088" r="8" opacity="0.4"/>
        <circle cx="690" cy="712" r="3" opacity="0.6"/>
        <circle cx="160" cy="850" r="3" opacity="0.5"/>
        <circle cx="460" cy="110" r="4" opacity="0.5"/>
        <circle cx="40" cy="470" r="3" opacity="0.5"/>
        <circle cx="92" cy="120" r="3" opacity="0.5"/>
        <circle cx="776" cy="24" r="3" opacity="0.6"/>
      </g>
    </svg>

    <h1 class="series-title">VENTURE</h1>

    <svg class="emblem-art" viewBox="0 0 644 576" role="img" aria-label="Ink-drawn sacred geometry mandala with nested circles, radiating lines and small orbs">
      <defs>
        <radialGradient id="emblemTone" cx="50%" cy="50%" r="50%">
          <stop offset="0%" stop-color="var(--art-light)"/>
          <stop offset="55%" stop-color="var(--art-mid)"/>
          <stop offset="100%" stop-color="var(--art-dark)"/>
        </radialGradient>
      </defs>
      <circle cx="322" cy="292" r="226" fill="url(#emblemTone)"/>
    </svg>

    <div class="emblem-number">482</div>

    <div class="edition" aria-label="Ascended">
      <span>A</span><span>S</span><span>C</span><span>E</span><span>N</span><span>D</span><span>E</span><span>D</span>
    </div>

    <div class="subtitle">
      <p class="subtitle-lead">SHAPING OUTCOMES</p>
      <p class="subtitle-body">Paths to unlocking</p>
      <p class="subtitle-body">cosmic truths</p>
    </div>

    <div class="author" aria-label="Dorian Pell">
      <span>D</span><span>O</span><span>R</span><span>I</span><span>A</span><span>N</span><span class="gap"></span><span>P</span><span>E</span><span>L</span><span>L</span>
    </div>
  </main>
</body>
</html>
```